Holiday Rental Company Flyer Design (DL not A5)

Note from Brandloom Administration: The category sizing selected is A5, however the project requires DL sized artwork. Please refer to the DL template link below while the 'Special Requirements' are updated accordingly.

Project Brief:
We need a double sided DL flyer designed for an up market Holiday Rental Company that portrays a personalised approach to property management. These are to be used for letter box drops to homes we're specifically targeting so the design should be modern, complimentary colour palette, uncluttered & visually appealing.

Please Download the DL Template from Quillora here: http://www.quillora.com.au/ql/ns/propath/UploadResources.aspx?selectedTab=0?pfid=KMT&pf_id=KMT&xnav=easypath-upload-image#Templates

Target Market(s)

Wealthy Home Owners

Industry/Entity Type

It Company

Other font styles liked:
• Avant Garde Extra Light & Demi

Colors
33b8a4

Requirements
Must have
• DL Flyer sizes (210mm width x 99mm width, plus 3mm bleed)
• Front: Logo, Main Image & Grab
• Back: Contact Details & Brief Description of our business
• Images: Ideally the main image should be the house with the pool but alternatively a lifestyle images could also be used.
Nice to have
• A creative designer!
Should not have
• Clutter & busy designs

```html
<!DOCTYPE html>
<html lang="en">
<head>
<meta charset="utf-8">
<title>Coastwillow Stays – DL Flyer</title>
<link rel="stylesheet" href="https://fonts.googleapis.com/css2?family=Questrial&family=Poppins:wght@300;400;600&display=swap">
<style>
  :root {
    --ink: #000000;
    --paper: #ffffff;
    --text-body: #d6d6d6;
    --text-title: #f0f0f0;
    --text-muted: #9a9a9a;
    --sky: #1f55a8;
    --stone: #c9b89a;
    --render: #e6e2da;
    --pool: #2f7fd0;
    --pool-deep: #1c5fa8;
    --shadow: rgba(0, 0, 0, 0.45);
  }
  * { margin: 0; padding: 0; box-sizing: border-box; }
  html, body {
    width: 1200px; height: 900px; overflow: hidden;
    background: radial-gradient(ellipse at center, #ffffff 55%, #e6e6e6 100%);
    font-family: "Questrial", "Poppins", sans-serif;
  }
  .canvas { position: relative; width: 1200px; height: 900px; }
  .flyer {
    position: absolute;
    background: var(--ink);
    box-shadow: 6px 8px 8px var(--shadow);
    color: var(--paper);
  }
  .flyer--front { left: 261px; top: 93px; width: 668px; height: 315px; }
  .flyer--back { left: 261px; top: 481px; width: 677px; height: 324px; }

  .brand {
    position: absolute;
    text-align: center;
    font-family: "Questrial", sans-serif;
    font-size: 13px;
    line-height: 17px;
    letter-spacing: 1.8px;
    color: var(--paper);
  }
  .brand__mark {
    display: block;
    width: 16px; height: 16px;
    margin: 6px auto 0;
    border: 1px solid var(--paper);
    border-radius: 50%;
  }
  .flyer--front .brand { left: 0; width: 135px; top: 74px; }
  .flyer--back .brand { left: 8px; width: 137px; top: 62px; }

  .tagline {
    position: absolute;
    text-align: center;
    font-family: "Poppins", sans-serif;
    font-weight: 300;
    font-size: 5.5px;
    line-height: 7px;
    color: var(--text-muted);
  }
  .flyer--front .tagline { left: 0; width: 135px; top: 268px; }
  .flyer--back .tagline { left: 0; width: 160px; top: 258px; }

  .hero-photo {
    position: absolute; left: 135px; top: 0; width: 533px; height: 315px;
    background: linear-gradient(180deg,
      var(--sky) 0%,
      var(--stone) 45%,
      var(--render) 78%,
      var(--pool) 84%,
      var(--pool-deep) 100%);
  }

  .about {
    position: absolute; left: 171px; top: 82px; width: 360px;
    font-family: "Poppins", sans-serif;
    font-weight: 300;
    color: var(--text-body);
  }
  .about__title { font-size: 10px; font-weight: 300; color: var(--text-title); margin-bottom: 26px; }
  .about p { font-size: 6.4px; line-height: 8px; margin-bottom: 8px; }

  .contact {
    position: absolute; left: 171px; top: 256px;
    font-family: "Poppins", sans-serif;
    font-weight: 600;
    font-size: 10px;
    color: var(--paper);
  }
  .contact__line { white-space: nowrap; word-spacing: 1px; }
  .contact__line span { margin-right: 10px; }
  .contact__address { margin-top: 11px; }
</style>
</head>
<body>
<main class="canvas">

  <section class="flyer flyer--front" aria-label="Flyer front">
    <div class="brand">COASTWILLOW<br>STAYS<span class="brand__mark"></span></div>
    <p class="tagline">Holiday Rental Management<br>with a difference</p>
    <div class="hero-photo" role="img" aria-label="Photo of a stone and white-rendered holiday villa under a blue sky with a tiled swimming pool in front"></div>
  </section>

  <section class="flyer flyer--back" aria-label="Flyer back">
    <div class="brand">COASTWILLOW<br>STAYS<span class="brand__mark"></span></div>
    <p class="tagline">Holiday Rental Management<br>with a difference</p>

    <div class="about">
      <h2 class="about__title">What we do differently!</h2>
      <p>Rather than relying upon a key safe or a central pickup destination,<br>a ‘Coastwillow Stays’ staff member will greet guests upon arrival.</p>
      <p>Our ‘Meet &amp; Greet’ service provides home owners with an increased level of Security and also allows us to:</p>
      <p>Prepare the home for their arrival (lights, heaters, music etc.)<br>Establish a rapport &amp; help facilitate future bookings<br>Reiterate their responsibilities to ensure the return of their bond</p>
      <p>If you’d like to know what your property could achieve or require additional information,<br>please contact us on:</p>
    </div>

    <div class="contact">
      <p class="contact__line"><span>t: (03)5900 4172</span><span>e: stay@coastwillowstays.com.au</span>w: coastwillowstays.com.au</p>
      <p class="contact__address">PO Box 48, Seacliff Victoria 3998</p>
    </div>
  </section>

</main>
</body>
</html>
```